Fine Art business needs new website

We need a simple website with a home page, about us page, New sculptures, Sold sculptures, and a contact us page.Our sculptures are very high end one of a kind pieces. As such we need the site to be VERY elegant and professional. Lastly, because I'll be updating pictures on the website on a monthly basis it needs to be user friendly to update (Wordpress is preferred). The only branding we have so far for the business is a business card.
Updates
I wasn't completely ready when this project launched, also I am on the road right now and haven't been able to be as responsive to all you designers as I would like. I will work on giving feedback to all the top designs we've received so far. Thank you all so much for your participation and hardwork.
Target Market(s)
High end customers (affluent), art collectors, interior decorators/designers
Industry/Entity Type
Art Gallery
Coding
Coded - Design and coding required
Number of Pages Required
5+ page
Requirements
Must have
- Easily editable picture gallery for myself so that I can add new pieces(pictures of the pieces), remove sold pieces, etc. I would like the website to be built in wordpress so I can update it. I currently use mangewordpress through Netmarro for my other business website and would like to do the same for this one.
- Pages:
- -Intro page with featured pieces
- -Current pieces gallery (for sale) mainly a picture gallery
- -Sculptures archive (sold pieces) another picture gallery
- -About us: Pull-down of -about the artist (attached content)
- -Artistic Process (attached content)
- -Show Schedule:
- -one page dedicated to "friends of TMV" (basically a link page)
- TO BE CLEAR "www.pineroverslane.com" IS A TOTALLY DIFFERENT SITE AND I'M NOT TRYING TO COMBINE THE TWO OR JOIN THEM INTO ONE. This page needs be more elegant and seperate from the Pine Rovers site.
- UPDATE: I'd like a link to the TMV Facebook page: https://www.faceplume-social.com/mirelcraftworks/
Nice to have
- I would like the pictures on the gallery pages able to have text connected with them (Materials, price)
- I would like the site style and fonts to be similar to our business cards we've already had designed (picture attached).
Should not have
- Too much flash or other things that will make the site slow to load.

```html
<!DOCTYPE html>
<html lang="en">
<head>
<meta charset="utf-8">
<title>Tidemark Vale — Home</title>
<link href="https://fonts.googleapis.com/css2?family=Poppins:wght@400;500;600;700&family=Cormorant+Garamond:wght@500&display=swap" rel="stylesheet">
<style>
:root{
  --purple:#5c3591;
  --purple-dark:#4a2878;
  --ink:#222;
  --grey:#6b6b6b;
  --white:#fff;
  --black:#000;
  --card-dark:#141414;
}
*{box-sizing:border-box;margin:0;padding:0}
html,body{width:1200px;height:3141px;overflow:hidden;background:var(--white);font-family:'Poppins',sans-serif;color:var(--ink)}
a{color:inherit;text-decoration:none}
.page{position:relative;width:1200px;height:3141px}

/* header */
.site-header{position:absolute;top:0;left:0;width:1200px;height:163px;background:var(--white)}
.brand{position:absolute;left:100px;top:52px;display:flex;align-items:center;gap:14px}
.brand-mark{width:34px;height:34px;background:var(--purple);border-radius:50%}
.brand-name{font-family:'Cormorant Garamond',serif;font-weight:500;font-size:30px;letter-spacing:3px;color:var(--purple)}
.search{position:absolute;left:770px;top:30px;display:flex;height:33px}
.search-field{width:192px;border:1px solid #bdbdbd;border-right:none;font-size:12px;color:#555;padding:8px 10px;font-family:inherit}
.search-btn{width:36px;background:var(--purple);display:flex;align-items:center;justify-content:center}
.cart{position:absolute;left:1033px;top:36px;display:flex;align-items:center;gap:8px;font-size:16px}
.main-nav{position:absolute;top:100px;right:102px;display:flex;gap:38px;font-size:16.5px;color:#333}

/* hero */
.hero{position:absolute;top:163px;left:0;width:1200px;height:623px}
.hero-photo{position:absolute;inset:0;background:radial-gradient(ellipse at 30% 50%,#6d6585 0%,#3b3550 35%,#1f1c26 70%),#29252f}
.hero-photo::after{content:"";position:absolute;inset:0;background:rgba(0,0,0,.25)}
.hero-content{position:absolute;top:200px;left:0;width:1200px;text-align:center;color:var(--white)}
.hero-title{font-size:45px;font-weight:700}
.hero-text{font-size:17.5px;font-weight:600;line-height:32px;margin-top:16px}
.btn{display:inline-flex;align-items:center;justify-content:center;background:var(--purple);color:var(--white);font-weight:600;border-radius:40px}
.hero .btn{width:245px;height:73px;font-size:18px;margin-top:28px}
.slider-dots{position:absolute;top:557px;left:0;width:1200px;display:flex;justify-content:center;gap:8px;align-items:center}
.dot{width:11px;height:11px;border-radius:50%;background:var(--white)}
.dot.active{width:17px;height:17px;border:2px solid var(--white);background:none;position:relative}
.dot.active::after{content:"";position:absolute;inset:3px;background:var(--white);border-radius:50%}

/* about */
.about{position:absolute;top:786px;left:0;width:1200px;height:392px;text-align:center}
.section-title{font-size:38px;font-weight:600;color:var(--purple)}
.about .section-title{margin-top:68px}
.about-text{width:820px;margin:22px auto 0;font-size:15.5px;line-height:30.5px;color:var(--grey)}
.about .btn{width:150px;height:47px;font-size:16px;margin-top:25px}

/* new sculptures */
.new-band{position:absolute;top:1178px;left:0;width:1200px;height:617px;background:var(--purple)}
.new-card{position:absolute;top:72px;left:95px;width:1008px;height:475px;background:var(--white)}
.new-card .section-title{position:absolute;left:62px;top:70px;font-size:36px}
.new-text{position:absolute;left:69px;top:140px;width:400px;font-size:14.5px;line-height:26.5px;color:#444}
.new-card .btn{position:absolute;left:69px;top:326px;width:184px;height:57px;font-size:17px}
.video{position:absolute;left:513px;top:78px;width:428px;height:322px;background:linear-gradient(135deg,#3a2a55,#6b4a96 45%,#2a2035)}
.play{position:absolute;left:179px;top:126px}

/* featured */
.featured{position:absolute;top:1795px;left:0;width:1200px;height:917px;text-align:center}
.featured .section-title{margin-top:70px;font-size:36px}
.pieces{position:absolute;top:162px;left:111px;display:grid;grid-template-columns:repeat(3,300px);gap:33px 37px}
.piece{position:relative;width:300px;height:321px;background:radial-gradient(ellipse at 50% 45%,#3d3d3d 0%,var(--card-dark) 60%)}
.piece.p1{background:radial-gradient(ellipse at 50% 40%,#1f5a44 0%,var(--card-dark) 55%)}
.piece.p2{background:radial-gradient(ellipse at 50% 35%,#3b2a5a 0%,var(--card-dark) 55%)}
.piece.p3{background:radial-gradient(ellipse at 50% 40%,#6a4a22 0%,var(--card-dark) 55%)}
.piece.p4{background:radial-gradient(ellipse at 50% 45%,#8a4a12 0%,var(--card-dark) 55%)}
.piece.p5{background:radial-gradient(ellipse at 50% 40%,#6b4a48 0%,var(--card-dark) 55%)}
.piece.p6{background:radial-gradient(ellipse at 50% 45%,#7a4a1a 0%,var(--card-dark) 55%)}
.piece-info{position:absolute;left:0;top:195px;width:100%;color:var(--white);text-align:center}
.piece-name{font-size:20px;font-weight:600}
.piece-price{font-size:20px;font-weight:600;margin-top:6px}

/* footer */
.site-footer{position:absolute;top:2712px;left:0;width:1200px;height:429px;background:var(--black);color:var(--white)}
.footer-col{position:absolute;top:50px}
.footer-title{font-size:22px;font-weight:600}
.col-contact{left:94px}
.contact-line{display:flex;gap:20px;align-items:center;font-size:17px;font-weight:500;margin-top:26px;line-height:35px}
.contact-line.phone{margin-top:14px}
.socials{display:flex;gap:13px;margin-top:30px}
.social{width:28px;height:28px;background:var(--white);border-radius:3px}
.col-quick{left:428px}
.col-other{left:636px}
.link-list{list-style:none;margin-top:20px;font-size:15px;line-height:32px}
.col-news{left:833px;width:272px}
.news-text{font-size:15px;line-height:28px;margin-top:18px}
.news-form{display:flex;margin-top:20px;height:39px}
.news-field{flex:1;background:var(--white);color:#777;font-size:12px;padding:11px 10px}
.news-btn{width:42px;background:var(--purple);display:flex;align-items:center;justify-content:center}
.copyright{position:absolute;top:370px;left:0;width:1200px;text-align:center;font-size:15px}
</style>
</head>
<body>
<div class="page">

<header class="site-header">
  <a class="brand" href="#"><span class="brand-mark"></span><span class="brand-name">TIDEMARK VALE</span></a>
  <form class="search">
    <span class="search-field">Search here..</span>
    <span class="search-btn"><svg width="15" height="15" viewBox="0 0 16 16"><circle cx="6.5" cy="6.5" r="4.5" fill="none" stroke="#fff" stroke-width="2"/><path d="M10 10l4 4" stroke="#fff" stroke-width="2.2" stroke-linecap="round"/></svg></span>
  </form>
  <a class="cart" href="#"><svg width="20" height="16" viewBox="0 0 20 16"><path d="M1 5h18l-2.5 10h-13z" fill="#5c3591"/><path d="M5 5l4-4M15 5l-4-4" stroke="#5c3591" stroke-width="1.6"/></svg>Cart</a>
  <nav class="main-nav">
    <a href="#">Home</a><a href="#">About Us</a><a href="#">New sculptures</a><a href="#">Sold Sculptures</a><a href="#">Contact Us</a>
  </nav>
</header>

<section class="hero">
  <div class="hero-photo" role="img" aria-label="Photograph of two split amethyst geodes"></div>
  <div class="hero-content">
    <h1 class="hero-title">Welcome to Tidemark Vale</h1>
    <p class="hero-text">Lorem ipsum dolor sit amet, consectetur adipiscing elit, sed do<br>eiusmod tempor incididunt ut labore et</p>
    <a class="btn" href="#">View More</a>
  </div>
  <div class="slider-dots"><span class="dot active"></span><span class="dot"></span><span class="dot"></span></div>
</section>

<section class="about">
  <h2 class="section-title">About Us</h2>
  <p class="about-text">Sed ut perspiciatis unde omnis iste natus error sit voluptatem accusantium doloremque laudantium, totam rem aperiam, eaque ipsa quae ab illo inventore veritatis et quasi architecto beatae vitae dicta sunt explicabo. Nemo enim ipsam voluptatem quia voluptas sit aspernatur aut odit aut fugit, sed quia consequuntur magni dolores eos qui ratione voluptatem sequi nesciunt.</p>
  <a class="btn" href="#">Read More</a>
</section>

<section class="new-band">
  <div class="new-card">
    <h2 class="section-title">New sculptures</h2>
    <p class="new-text">Sed ut perspiciatis unde omnis iste natus error sit voluptatem accusantium doloremque laudantium, totam rem aperiam, eaque ipsa quae ab illo inventore veritatis et quasi architecto beatae vitae dicta sunt explicabo. Nemo enim ipsam voluptatem quia voluptas sit aspernatur aut odit aut fugit, sed quia consequuntur magni</p>
    <a class="btn" href="#">Watch Video</a>
    <div class="video" role="img" aria-label="Video still of amethyst geode sculptures">
      <svg class="play" width="72" height="72" viewBox="0 0 72 72"><circle cx="36" cy="36" r="33" fill="none" stroke="#fff" stroke-width="3"/><path d="M29 22v28l22-14z" fill="none" stroke="#fff" stroke-width="3" stroke-linejoin="round"/></svg>
    </div>
  </div>
</section>

<section class="featured">
  <h2 class="section-title">Featured Pieces</h2>
  <div class="pieces">
    <div class="piece p1" role="img" aria-label="Green malachite sculpture on a pedestal"></div>
    <div class="piece p2" role="img" aria-label="Amethyst geode sculpture on a pedestal">
      <div class="piece-info"><p class="piece-name">Accounting Services</p><p class="piece-price">$ 48.00</p></div>
    </div>
    <div class="piece p3" role="img" aria-label="Carved ammonite fossil sculpture"></div>
    <div class="piece p4" role="img" aria-label="Polished amber agate sculpture"></div>
    <div class="piece p5" role="img" aria-label="Rough crystal cluster sculpture on a stand"></div>
    <div class="piece p6" role="img" aria-label="Spiral ammonite sculpture on a base"></div>
  </div>
</section>

<footer class="site-footer">
  <div class="footer-col col-contact">
    <h3 class="footer-title">Contact Us</h3>
    <div class="contact-line">
      <svg width="22" height="30" viewBox="0 0 22 30"><path d="M11 1C5.5 1 1 5.3 1 10.8 1 18 11 29 11 29s10-11 10-18.2C21 5.3 16.5 1 11 1z" fill="#5c3591"/><circle cx="11" cy="11" r="4" fill="#000"/></svg>
      <span>PO box 440218<br>Ridgecrest Falls CO 80999</span>
    </div>
    <div class="contact-line phone">
      <svg width="22" height="22" viewBox="0 0 22 22"><path d="M3 13v-2a8 8 0 0 1 16 0v2" fill="none" stroke="#5c3591" stroke-width="2.2"/><rect x="1" y="12" width="5" height="8" rx="1.5" fill="#5c3591"/><rect x="16" y="12" width="5" height="8" rx="1.5" fill="#5c3591"/></svg>
      <span>+1.5550142298</span>
    </div>
    <div class="socials"><a class="social" href="https://www.faceplume-social.com/mirelcraftworks/" aria-label="Social page"></a><a class="social" href="#" aria-label="Social page"></a><a class="social" href="#" aria-label="Social page"></a><a class="social" href="#" aria-label="Social page"></a></div>
  </div>
  <div class="footer-col col-quick">
    <h3 class="footer-title">Quick Links</h3>
    <ul class="link-list"><li>Home</li><li>About Us</li><li>New sculptures</li><li>Sold Sculptures</li><li>Contact Us</li></ul>
  </div>
  <div class="footer-col col-other">
    <h3 class="footer-title">Other Links</h3>
    <ul class="link-list"><li>Terms &amp; Conditions</li><li>Privacy Policy</li></ul>
  </div>
  <div class="footer-col col-news">
    <h3 class="footer-title">Newsletter</h3>
    <p class="news-text">But I must explain to you how all this mistaken idea of denouncing pleasure and praising.</p>
    <form class="news-form"><span class="news-field">Enter your email address</span><span class="news-btn"><svg width="12" height="10" viewBox="0 0 12 10"><path d="M1 5h9M6 1l4 4-4 4" fill="none" stroke="#fff" stroke-width="1.8"/></svg></span></form>
  </div>
  <p class="copyright">© 2018 Copyrights | All Rights Reserved</p>
</footer>

</div>
</body>
</html>
```